Redesign of business card for Cedar Ridge Mechanical

We are looking for a new design for our business cards for Cedar Ridge Mechanical. We are a plumbing & HVAC construction company, operating on the West Coast of Canada and USA. Logo attached.
Industry/Entity Type
Construction - Plumbing & HVAC
Contact Information for Business Card
Name, address, phone numbers, email, website address
Look and feel
Each slider illustrates characteristics of the customer's brand and the style your logo design should communicate.

```html
<!DOCTYPE html>
<html lang="en">
<head>
<meta charset="utf-8">
<title>Cedar Ridge Mechanical — Business Card</title>
<link rel="stylesheet" href="https://fonts.googleapis.com/css2?family=Montserrat:wght@400;500;600;700&display=swap">
<style>
  :root {
    --backdrop: #e6e3de;
    --card-light: #ffffff;
    --card-dark: #252525;
    --ink: #1e1c1c;
    --ink-soft: #2a2828;
    --paper-ink: #ffffff;
  }
  * { margin: 0; padding: 0; box-sizing: border-box; }
  html, body { width: 900px; height: 1200px; overflow: hidden; }
  body {
    background: var(--backdrop);
    font-family: "Montserrat", Arial, sans-serif;
    color: var(--ink);
    position: relative;
  }
  .card {
    position: absolute;
    border-radius: 22px;
    box-shadow: 0 6px 18px rgba(0,0,0,0.18);
  }
  .card--front { left: 80px; top: 131px; width: 742px; height: 440px; background: var(--card-light); }
  .card--back  { left: 78px; top: 640px; width: 744px; height: 438px; background: var(--card-dark); }

  .brand-name {
    position: absolute;
    font-weight: 700;
    letter-spacing: 0.5px;
    line-height: 1.05;
  }
  .card--front .brand-name {
    left: 122px; top: 172px;
    font-size: 27px; color: var(--ink);
  }
  .card--back .brand-name {
    left: 0; right: 0; top: 168px;
    text-align: center;
    font-size: 44px; color: var(--paper-ink);
  }

  .divider {
    position: absolute; left: 356px; top: 156px;
    width: 2px; height: 146px; background: var(--ink);
  }
  .person { position: absolute; left: 374px; top: 150px; }
  .person__name { font-size: 25px; font-weight: 700; color: var(--ink); }
  .person__title { font-size: 15.5px; font-weight: 500; color: var(--ink-soft); margin-top: 2px; }

  .contacts { position: absolute; left: 374px; top: 225px; list-style: none; }
  .contacts li {
    display: flex; align-items: center; gap: 11px;
    height: 30px; font-size: 15.5px; font-weight: 500; color: var(--ink-soft);
  }
  .contacts svg { width: 16px; height: 16px; fill: var(--ink); flex: none; }

  .address {
    position: absolute; left: 0; right: 0; top: 374px;
    text-align: center; font-size: 15.5px; font-weight: 500; color: var(--ink-soft);
  }
</style>
</head>
<body>
  <section class="card card--front">
    <div class="brand-name">Cedar Ridge<br>Mechanical</div>
    <div class="divider"></div>
    <div class="person">
      <div class="person__name">Dana Whitlock</div>
      <div class="person__title">Managing Director</div>
    </div>
    <ul class="contacts">
      <li>
        <svg viewBox="0 0 24 24" aria-hidden="true"><path d="M6.6 10.8a15.1 15.1 0 0 0 6.6 6.6l2.2-2.2a1 1 0 0 1 1-.25 11.4 11.4 0 0 0 3.6.57 1 1 0 0 1 1 1V20a1 1 0 0 1-1 1A17 17 0 0 1 3 4a1 1 0 0 1 1-1h3.5a1 1 0 0 1 1 1c0 1.25.2 2.45.57 3.57a1 1 0 0 1-.25 1z"/></svg>
        555.214.7730
      </li>
      <li>
        <svg viewBox="0 0 24 24" aria-hidden="true"><path d="M3 5h18v14H3z M3 6l9 6 9-6" fill="none" stroke="#1e1c1c" stroke-width="0"/><path d="M3 5h18v2l-9 6-9-6z"/><path d="M3 9l9 6 9-6v10H3z"/></svg>
        info@cedarridgemech.com
      </li>
      <li>
        <svg viewBox="0 0 24 24" aria-hidden="true"><path d="M12 2a10 10 0 1 0 0 20 10 10 0 0 0 0-20zm0 2a8 8 0 0 1 6.9 4H15l-2 2 1 3-2 2v3l-2-1v-4l-3-2V8l3-1V4.1c.7-.1 1.3-.1 2-.1z"/></svg>
        www.cedarridgemech.com
      </li>
    </ul>
    <div class="address">48 Harbor Pine Road Fairview, WA 98210</div>
  </section>

  <section class="card card--back">
    <div class="brand-name">Cedar Ridge Mechanical</div>
  </section>
</body>
</html>
```